Vantiqo custom business card design

Need a authentic, innovative business card design for a new mobile app business. I am uploading a few screen images from our app for you to view. I would like app design theme to match business card design. I can also send logo images.

```html
<!DOCTYPE html>
<html lang="en">
<head>
<meta charset="utf-8">
<title>Vantiqo Business Card</title>
<link href="https://fonts.googleapis.com/css2?family=Open+Sans:wght@400;600;700&display=swap" rel="stylesheet">
<style>
  :root {
    --backdrop: #e9e6e3;
    --card-dark: #1b1d20;
    --card-light: #ffffff;
    --ink: #3a3a3a;
    --silver: #a9abae;
    --violet: #5e1a9c;
    --divider: #b9b9b9;
  }
  * { margin: 0; padding: 0; box-sizing: border-box; }
  html, body {
    width: 1200px; height: 864px; overflow: hidden;
    background: var(--backdrop);
    font-family: "Open Sans", Arial, sans-serif;
  }
  .canvas {
    position: relative; width: 1200px; height: 864px;
    display: flex; align-items: center; justify-content: center; gap: 48px;
  }
  .card {
    width: 520px; height: 297px;
    border-radius: 4px;
    box-shadow: 0 10px 28px rgba(0,0,0,0.18);
    position: relative;
  }
  .card-front {
    background: var(--card-dark);
    display: flex; flex-direction: column; align-items: center; justify-content: center;
  }
  .brand {
    display: flex; align-items: center; gap: 14px;
  }
  .brand-dot {
    width: 34px; height: 34px; border-radius: 50%;
    background: var(--silver);
  }
  .brand-name {
    font-weight: 700; font-size: 46px; letter-spacing: 0.5px;
    color: var(--silver);
  }
  .front-url {
    margin-top: 26px;
    font-size: 14px; letter-spacing: 7px;
    color: var(--silver);
  }
  .card-back {
    background: var(--card-light);
    display: flex; align-items: center;
    padding: 0 34px 0 38px;
  }
  .back-brand {
    width: 200px;
    display: flex; align-items: center; gap: 12px;
  }
  .back-brand .brand-dot { background: var(--violet); width: 30px; height: 30px; }
  .back-brand .brand-name { color: var(--ink); font-size: 36px; }
  .divider {
    width: 1px; height: 190px; margin: 0 26px 0 24px;
    background: linear-gradient(to bottom, transparent, var(--divider) 30%, var(--divider) 70%, transparent);
  }
  .details { color: var(--ink); font-size: 14px; line-height: 1.45; }
  .person-name { color: var(--violet); font-weight: 700; font-size: 22px; line-height: 1.1; }
  .person-role { font-size: 14px; letter-spacing: 0.5px; margin-bottom: 8px; }
  .address { margin-bottom: 8px; }
  .contact-list { list-style: none; }
  .contact-list b { color: var(--violet); font-weight: 700; margin-right: 4px; }
</style>
</head>
<body>
<main class="canvas">
  <section class="card card-front">
    <div class="brand">
      <span class="brand-dot"></span>
      <span class="brand-name">Vantiqo</span>
    </div>
    <p class="front-url">www.vantiqo.com</p>
  </section>

  <section class="card card-back">
    <div class="back-brand">
      <span class="brand-dot"></span>
      <span class="brand-name">Vantiqo</span>
    </div>
    <div class="divider"></div>
    <div class="details">
      <p class="person-name">MARCUS HALE</p>
      <p class="person-role">PRESIDENT</p>
      <p class="address">4127 Alderbrook Lane<br>Cedar Hollow, NY 12048</p>
      <ul class="contact-list">
        <li><b>P:</b>555 0148 2271</li>
        <li><b>M:</b>555 0193 6402</li>
        <li><b>F:</b>555 0126 7815</li>
        <li><b>E:</b>marcus@vantiqo.com</li>
        <li><b>W:</b>www.vantiqo.com</li>
      </ul>
    </div>
  </section>
</main>
</body>
</html>
```